my website is tavorinque.com. (brand name is ta belle vitrine) This is just a template that i have choose for. The content and the pictures are not about my business just the template.
I would like to have 4 pages for now. 1 homepage, which will be an overview for all pages, it is right now in this way. It will directly highlight my story. My website will tell an exclusive story about details which makes the difference and will make people happy with very small things. It will be art related but very stylish as well. I also want to have a event agenda on my homepage where people can see where my next event is. Page 2 my blog, where I will write weekly about mindset, lifestyle and details. Inspiration place for people who are looking for unique and exclusive approaches in life. Page 3 shop, where I will sell my stuff which is handmade and unique, it will be limited edition stuff. Mostly I will make the designs from marbling art, which I am a teacher for. (https://www.vidoranta.com/watch?v=KpwuzRaxTmo) check this video out for more. Page 4 is book page. Here people will be able to book private or group classes for marbling art (check the video). I have already a community of more than 500 people on gath rix, which will be my public as well. I wanna implement the gath rix button on this page as well. to be able to track.

This is about my website. I also need a logo for my brand, which will suit my website and my goals.

I can also give you a reference website, which really like as structure and style;
https://www.brightorvalco.com/products/the-morning-ledger?gclid=Xr4TpLmwq2HsVD9KEBsZTrc-WkPhyQ-uvlEjdRs3NKaOYFCBWMpuTzG8xyCVbhdnLWRqoaNf_2e8ZtpRvHbAwq9FLQ_hqgQ

Logo Text

ta belle vitrine

Coding

Coded - Design and coding required

Number of Pages Required

4 page

Requirements
Must have
• I can also give you a reference website, which really like as structure and style;
• https://www.brightorvalco.com/products/the-morning-ledger?gclid=Xr4TpLmwq2HsVD9KEBsZTrc-WkPhyQ-uvlEjdRs3NKaOYFCBWMpuTzG8xyCVbhdnLWRqoaNf_2e8ZtpRvHbAwq9FLQ_hqgQ

```html
<!DOCTYPE html>
<html lang="en">
<head>
<meta charset="utf-8">
<title>ta belle vitrine — Contact</title>
<link href="https://fonts.googleapis.com/css2?family=Montserrat:wght@400;500;600&family=Lato:wght@400&display=swap" rel="stylesheet">
<style>
  :root {
    --ink: #000;
    --paper: #fff;
    --text: #555;
    --muted: #888;
    --border: #7a7a7a;
  }
  * { box-sizing: border-box; margin: 0; padding: 0; }
  html, body { width: 1200px; height: 1199px; overflow: hidden; background: var(--paper); }
  body { position: relative; font-family: "Lato", sans-serif; color: var(--text); }
  .abs { position: absolute; }

  .newsletter { left: 0; top: 58px; width: 1200px; height: 187px; background: var(--ink); }
  .newsletter-title { left: 238px; top: 54px; font-family: "Montserrat", sans-serif; font-weight: 600; font-size: 13px; color: var(--paper); letter-spacing: .3px; }
  .email-field { left: 235px; top: 90px; width: 579px; height: 38px; border: 1px solid var(--paper); }
  .email-field svg { position: absolute; left: 21px; top: 14px; }
  .email-field span { position: absolute; left: 54px; top: 11px; font-family: "Montserrat", sans-serif; font-weight: 600; font-size: 10px; color: var(--paper); letter-spacing: .3px; }
  .subscribe-btn { left: 836px; top: 90px; width: 129px; height: 38px; background: var(--paper); color: var(--ink); font-family: "Montserrat", sans-serif; font-weight: 500; font-size: 10px; display: flex; align-items: center; justify-content: center; letter-spacing: .3px; }

  .contact-title { left: 0; width: 1200px; top: 298px; text-align: center; font-family: "Montserrat", sans-serif; font-weight: 500; font-size: 18px; color: var(--ink); letter-spacing: .6px; }
  .contact-sub { left: 0; width: 1200px; top: 329px; text-align: center; font-family: "Montserrat", sans-serif; font-size: 10px; color: var(--muted); letter-spacing: 1.3px; }
  .contact-rule { left: 536px; top: 357px; width: 128px; height: 1px; background: var(--ink); }
  .intro { left: 0; width: 1206px; top: 411px; text-align: center; font-size: 10.5px; line-height: 19px; letter-spacing: .9px; white-space: nowrap; }

  .info { width: 300px; text-align: center; font-size: 10.5px; line-height: 19px; letter-spacing: 1px; }
  .info svg { display: block; margin: 0 auto 15px; }

  .field { border: 1px solid var(--border); font-size: 10.5px; letter-spacing: 1px; color: var(--text); padding: 11px 0 0 16px; }
  .submit-btn { left: 911px; top: 831px; width: 128px; height: 38px; background: var(--ink); color: var(--paper); font-family: "Montserrat", sans-serif; font-weight: 600; font-size: 10px; display: flex; align-items: center; justify-content: center; }

  .footer { left: 0; top: 929px; width: 1200px; height: 270px; background: var(--ink); }
  .social { left: 0; width: 1200px; top: 154px; display: flex; justify-content: center; gap: 30px; padding-left: 3px; }
  .social span { width: 10px; height: 10px; border-radius: 50%; background: var(--paper); }
  .copyright { left: 0; width: 1206px; top: 196px; text-align: center; font-family: "Montserrat", sans-serif; font-weight: 600; font-size: 10px; color: var(--paper); }
</style>
</head>
<body>
  <section class="abs newsletter">
    <h2 class="abs newsletter-title">SUBSCRIBE TO OUR NEWSLETTER</h2>
    <div class="abs email-field">
      <svg width="11" height="9" viewBox="0 0 11 9" fill="none" stroke="#fff" stroke-width="1"><rect x=".5" y=".5" width="10" height="8"/><path d="M.5 .5l5 4 5-4M.5 8.5l3.5-3.5M10.5 8.5L7 5"/></svg>
      <span>EMAIL ADDRESS</span>
    </div>
    <div class="abs subscribe-btn">SUBSCRIBE</div>
  </section>

  <h2 class="abs contact-title">CONTACT US</h2>
  <p class="abs contact-sub">WE LOVE TALKING</p>
  <div class="abs contact-rule"></div>
  <p class="abs intro">Donec rutrum congue leo eget malesuada. Curabitur non nulla sit amet nisl tempus convallis<br>quis ac lectus. Sed porttitor lectus nibh. Proin eget tortor risus. Nulla porttitor accumsan tincidunt.<br>Nulla porttitor accumsan tincidunt.</p>

  <div class="abs info" style="left:151px;top:526px;">
    <svg width="21" height="18" viewBox="0 0 21 18"><rect x="1" y="1" width="19" height="12" fill="none" stroke="#000" stroke-width="2"/><rect x="7" y="15" width="7" height="2" fill="#000"/><rect x="9.5" y="13" width="2" height="3" fill="#000"/></svg>
    hello@tavorinque.com
  </div>
  <div class="abs info" style="left:453px;top:526px;">
    <svg width="21" height="18" viewBox="0 0 21 18"><path d="M10.5 0L0 9h3v9h6v-6h3v6h6V9h3z" fill="#000"/></svg>
    48 Larkwell Lane<br>Brindle, TX 79310
  </div>
  <div class="abs info" style="left:756px;top:526px;">
    <svg width="20" height="18" viewBox="0 0 20 18"><path d="M16 0l3 3.5c.5.6.4 1.4-.2 2C13 12 9 16 3 18.2c-.7.2-1.3 0-1.7-.5L0 15.3l3.8-3 2.3 1.8C9 12.5 11.5 10 13 7l-1.8-2.4z" fill="#000"/></svg>
    +000 - 482 - 615 - 903
  </div>

  <div class="abs field" style="left:161px;top:649px;width:429px;height:38px;">Subject*</div>
  <div class="abs field" style="left:161px;top:708px;width:429px;height:38px;">Name*</div>
  <div class="abs field" style="left:161px;top:766px;width:429px;height:38px;">Email*</div>
  <div class="abs field" style="left:610px;top:649px;width:429px;height:155px;padding-left:21px;">Message</div>
  <div class="abs submit-btn">SUBMIT</div>

  <footer class="abs footer">
    <div class="abs social" aria-label="Social links">
      <span></span><span></span><span></span><span></span><span></span>
    </div>
    <p class="abs copyright">© 2017 - ta belle vitrine. All Right Reserved</p>
  </footer>
</body>
</html>
```